Corvane Paintless Dent Removal

Our company works on vehicles removing dents using a highly skilled trade which the metal is massaged out with special tools without disturbing the original paint, hence paintless dent removal. Besides keeping the paint and metal original its also very environmentally friendly since no paint or toxic fillers are used. Also we we are one of the most experienced companies in the business with 25 years

Target Market(s)

Retail Automobile consumers, Auto Dealerships and Auto Body Shops

Industry/Entity Type

Auto Repair

Contact Information for Business Card

Dale Hollister
PO Box 518 Brookmere, NY 11962
631-555-0148
corvanepdr@mailbox-example.com
website corvanepdr.example
youtube corvane paintless dent removal
25 years of experience removing Dents, Dings and Hail Damage

Font styles to use
Serif
Sans Serif

Colors

Designer to choose colors to be used in the design.

Requirements
Must have
• I do like things that are simple but classy and somewhat bold, also I like my logo so that should be somewhat important

```html
<!DOCTYPE html>
<html lang="en">
<head>
<meta charset="utf-8">
<title>Corvane Paintless Dent Removal — Business Card</title>
<link href="https://fonts.googleapis.com/css2?family=Roboto:wght@400;500&family=Roboto+Condensed:wght@700&display=swap" rel="stylesheet">
<style>
  :root {
    --navy: #13294b;
    --green: #7dbb22;
    --gold: #c9962e;
    --paper: #f6f6f4;
    --ink: #3a3a3a;
    --rule: #8a8a8a;
    --backdrop: #e4e4e2;
  }
  * { margin: 0; padding: 0; box-sizing: border-box; }
  html, body {
    width: 1200px; height: 960px; overflow: hidden;
    background: var(--backdrop);
    font-family: "Roboto", Arial, sans-serif;
  }
  .canvas { position: relative; width: 1200px; height: 960px; }

  .card { position: absolute; width: 600px; height: 343px; overflow: hidden; }
  .card-front { left: 314px; top: 113px; background: var(--paper); }
  .card-back { left: 311px; top: 472px; background: var(--navy); }

  .side-band { position: absolute; left: 0; top: 0; width: 30px; height: 343px; }

  .experience-seal {
    position: absolute; left: 62px; top: 40px;
    width: 76px; height: 76px; border-radius: 50%;
    background: #111; border: 4px solid var(--gold);
    color: var(--gold); text-align: center;
    font-family: "Roboto Condensed", Arial, sans-serif; font-weight: 700;
  }
  .experience-seal .years-number { display: block; font-size: 26px; line-height: 1; margin-top: 12px; }
  .experience-seal .years-label { display: block; font-size: 10px; letter-spacing: 0.5px; margin-top: 2px; color: #fff; }

  .wordmark {
    position: absolute; display: flex; align-items: center; gap: 10px;
    font-family: "Roboto Condensed", Arial, sans-serif; font-weight: 700;
  }
  .wordmark .mark-dot { width: 18px; height: 18px; border-radius: 50%; background: var(--green); flex: none; }
  .wordmark .mark-name { display: block; line-height: 1; }
  .wordmark .mark-name span { display: block; }
  .wordmark-front { right: 36px; top: 56px; color: var(--navy); }
  .wordmark-front .name-main { font-size: 34px; letter-spacing: 0.5px; }
  .wordmark-front .name-sub { font-size: 15px; margin-top: 3px; }
  .wordmark-back { left: 50%; top: 136px; transform: translateX(-50%); color: #fff; }
  .wordmark-back .name-main { font-size: 40px; letter-spacing: 0.5px; }
  .wordmark-back .name-sub { font-size: 18px; margin-top: 3px; }

  .holder-name {
    position: absolute; left: 58px; top: 207px;
    font-family: "Roboto Condensed", Arial, sans-serif; font-weight: 700;
    font-size: 22px; color: var(--navy); text-transform: uppercase;
  }
  .name-rule { position: absolute; left: 57px; top: 240px; width: 505px; height: 1px; background: var(--rule); }

  .contact-list { position: absolute; left: 58px; top: 255px; list-style: none; font-size: 14px; color: var(--ink); }
  .contact-list li { display: flex; align-items: center; gap: 9px; height: 19px; }
  .contact-list svg { width: 13px; height: 13px; flex: none; fill: var(--navy); }

  .mail-address {
    position: absolute; right: 36px; top: 258px; text-align: right;
    font-size: 14px; line-height: 18px; color: var(--ink); font-style: normal;
  }

  .back-url {
    position: absolute; left: 0; right: 0; top: 280px; text-align: center;
    color: #fff; font-size: 14px; letter-spacing: 6px;
  }
</style>
</head>
<body>
<main class="canvas">
  <section class="card card-front" aria-label="Business card front">
    <svg class="side-band" viewBox="0 0 30 343" aria-hidden="true">
      <polygon points="0,0 30,0 30,143 0,136" fill="#7dbb22"/>
      <polygon points="0,136 30,143 30,146 0,139" fill="#ffffff"/>
      <polygon points="0,139 30,146 30,343 0,343" fill="#13294b"/>
    </svg>

    <div class="experience-seal" aria-label="25 years of experience">
      <span class="years-number">25</span>
      <span class="years-label">YEARS</span>
    </div>

    <div class="wordmark wordmark-front">
      <span class="mark-dot"></span>
      <span class="mark-name"><span class="name-main">CORVANE</span><span class="name-sub">Paintless Dent Removal</span></span>
    </div>

    <h1 class="holder-name">Dale Hollister</h1>
    <div class="name-rule"></div>

    <ul class="contact-list">
      <li><svg viewBox="0 0 24 24"><path d="M6.6 10.8a15.1 15.1 0 0 0 6.6 6.6l2.2-2.2a1 1 0 0 1 1-.25 11.4 11.4 0 0 0 3.6.57 1 1 0 0 1 1 1V20a1 1 0 0 1-1 1A17 17 0 0 1 3 4a1 1 0 0 1 1-1h3.5a1 1 0 0 1 1 1c0 1.25.2 2.45.57 3.57a1 1 0 0 1-.25 1z"/></svg>631-555-0148</li>
      <li><svg viewBox="0 0 24 24"><path d="M2 5h20v14H2z M3.5 6.5v1l8.5 5.5 8.5-5.5v-1L12 11.8z" fill-rule="evenodd"/></svg>corvanepdr@mailbox-example.com</li>
      <li><svg viewBox="0 0 24 24"><rect x="2" y="5" width="20" height="14" rx="3"/></svg>corvane paintless dent removal</li>
    </ul>

    <address class="mail-address">
      PO Box 518<br>
      Brookmere, NY 11962<br>
      www.corvanepdr.example
    </address>
  </section>

  <section class="card card-back" aria-label="Business card back">
    <div class="wordmark wordmark-back">
      <span class="mark-dot"></span>
      <span class="mark-name"><span class="name-main">CORVANE</span><span class="name-sub">Paintless Dent Removal</span></span>
    </div>
    <p class="back-url">www.corvanepdr.example</p>
  </section>
</main>
</body>
</html>
```